NEW Modern Sleek Business Card for VR Language Startup

Our startup is using VR to lead the next wave of world language education. We need a two-sided business card that introduces the larger organization (Brightloom Language Inc) and our contact info on one side and shows the product, Glimwoorld, on the other side.

Side 1 (contact info)= Brightloom Logo and Contact info (name, title, phone, email)

Side 2 (product)= Glimworld logo, text, and website
Text= Culturally Immersive Language Learning Games
Website= www.glimworld-play.com

Target Market(s)

Education, Technology

Contact Information for Business Card

Contact info will be updated upon approval of the design. For now, put this as a placeholder.

Perry Dunmore
Founder & CEO
pdunmore@quillpost-mail.net
(555)-014-2286

Font styles to use
Other font styles liked:
• Gibson and Century Gothic are the brand fonts

Requirements
Nice to have
• I would love to see cohesion between the design and colors of the two logos. I have attached a few business card designs that I like, so you can get a feel for my preferred style.

```html
<!DOCTYPE html>
<html lang="en">
<head>
<meta charset="utf-8">
<title>Brightloom Language – Business Card</title>
<link href="https://fonts.googleapis.com/css2?family=Montserrat:wght@500;700&family=Didact+Gothic&display=swap" rel="stylesheet">
<style>
  :root {
    --bg: #e9e9ec;
    --orange: #f7a531;
    --red: #ef3355;
    --magenta: #a3319a;
    --violet: #7e5fb2;
    --cyan: #46c9dc;
    --blue: #3a7fd6;
    --white: #ffffff;
    --ink: #4a4a52;
    --card-w: 620px;
    --card-h: 354px;
    --radius: 30px;
  }
  * { box-sizing: border-box; margin: 0; padding: 0; }
  html, body { width: 1200px; height: 900px; overflow: hidden; }
  body {
    background: var(--bg);
    font-family: "Didact Gothic", "Century Gothic", sans-serif;
    display: flex; flex-direction: column; align-items: center; justify-content: center;
    gap: 52px;
  }
  .card {
    position: relative;
    width: var(--card-w); height: var(--card-h);
    border-radius: var(--radius);
    overflow: hidden;
    box-shadow: 0 14px 34px rgba(0,0,0,.18);
  }

  /* Side 1 – contact */
  .card--contact {
    background: linear-gradient(115deg, var(--orange) 0%, var(--red) 28%, var(--magenta) 58%, var(--violet) 78%, var(--cyan) 100%);
    color: var(--white);
  }
  .contact__name {
    position: absolute; left: 72px; top: 58px;
    display: flex; align-items: baseline; gap: 16px;
  }
  .contact__person { font-family: "Montserrat", sans-serif; font-weight: 700; font-size: 15px; letter-spacing: .42em; }
  .contact__title { font-family: "Montserrat", sans-serif; font-weight: 500; font-size: 8px; letter-spacing: .22em; }
  .brand {
    position: absolute; left: 72px; top: 128px;
    display: flex; align-items: center; gap: 16px;
  }
  .brand__dot { width: 58px; height: 58px; border-radius: 50%; background: var(--white); }
  .brand__name { font-family: "Montserrat", sans-serif; font-weight: 700; font-size: 30px; letter-spacing: .06em; line-height: 1.05; }
  .contact__line {
    position: absolute; display: flex; align-items: center; gap: 12px;
    font-size: 15px; letter-spacing: .16em; white-space: nowrap;
  }
  .contact__line--phone { right: 44px; top: 216px; }
  .contact__line--email { left: 44px; bottom: 38px; }
  .icon { width: 24px; height: 24px; flex: none; }

  /* Side 2 – product */
  .card--product { background: var(--white); color: var(--ink); }
  .art-area { position: absolute; }
  .art-area--left {
    left: 0; top: 0; bottom: 0; width: 120px;
    background: linear-gradient(180deg, var(--orange) 0%, var(--red) 35%, var(--violet) 70%, var(--cyan) 100%);
  }
  .art-area--right {
    right: 0; top: 110px; bottom: 0; width: 64px;
    background: linear-gradient(180deg, var(--orange) 0%, var(--red) 40%, var(--violet) 70%, var(--blue) 100%);
  }
  .product {
    position: absolute; left: 120px; right: 64px; top: 62px;
    display: flex; flex-direction: column; align-items: center;
  }
  .product__mark { display: flex; align-items: center; gap: 12px; }
  .product__dot { width: 44px; height: 44px; border-radius: 50%; background: var(--blue); }
  .product__name { font-family: "Montserrat", sans-serif; font-weight: 700; font-size: 38px; color: var(--blue); letter-spacing: .01em; }
  .product__tagline {
    margin-top: 18px; text-align: center;
    font-size: 14px; letter-spacing: .34em; line-height: 1.55; color: var(--ink);
  }
  .product__web {
    position: absolute; left: 120px; right: 64px; bottom: 40px;
    display: flex; justify-content: center; align-items: center; gap: 16px;
    font-size: 16px; letter-spacing: .26em; color: var(--ink); white-space: nowrap;
  }
</style>
</head>
<body>

  <section class="card card--contact" aria-label="Brightloom Language contact side">
    <div class="contact__name">
      <span class="contact__person">PERRY DUNMORE</span>
      <span class="contact__title">FOUNDER &amp; CEO</span>
    </div>

    <div class="brand">
      <span class="brand__dot" aria-hidden="true"></span>
      <span class="brand__name">BRIGHTLOOM<br>LANGUAGE</span>
    </div>

    <div class="contact__line contact__line--phone">
      <svg class="icon" viewBox="0 0 24 24" aria-hidden="true">
        <circle cx="12" cy="12" r="12" fill="#fff"/>
        <path d="M8.6 6.5l2 2.3-1.1 1.4c.8 1.7 2 2.9 3.6 3.7l1.4-1.1 2.3 2-1.2 1.9c-4.1-.3-8.2-4.4-8.6-8.6z" fill="#7e5fb2"/>
      </svg>
      <span>(555)-014-2286</span>
    </div>

    <div class="contact__line contact__line--email">
      <svg class="icon" viewBox="0 0 24 24" aria-hidden="true">
        <circle cx="12" cy="12" r="12" fill="#fff"/>
        <rect x="6" y="8" width="12" height="8.5" rx="1" fill="#a3319a"/>
        <path d="M6.4 8.6l5.6 4.4 5.6-4.4" fill="none" stroke="#fff" stroke-width="1.2"/>
      </svg>
      <span>pdunmore@quillpost-mail.net</span>
    </div>
  </section>

  <section class="card card--product" aria-label="Glimworld product side">
    <div class="art-area art-area--left" role="img" aria-label="Area for gradient edge artwork"></div>
    <div class="art-area art-area--right" role="img" aria-label="Area for gradient edge artwork"></div>

    <div class="product">
      <div class="product__mark">
        <span class="product__dot" aria-hidden="true"></span>
        <span class="product__name">Glimworld</span>
      </div>
      <p class="product__tagline">CULTURALLY IMMERSIVE<br>LANGUAGE LEARNING GAMES</p>
    </div>

    <div class="product__web">
      <svg class="icon" viewBox="0 0 24 24" aria-hidden="true">
        <circle cx="12" cy="12" r="11" fill="#4a4a52"/>
        <g fill="none" stroke="#fff" stroke-width="1">
          <circle cx="12" cy="12" r="6.5"/>
          <ellipse cx="12" cy="12" rx="3" ry="6.5"/>
          <path d="M5.5 12h13M6.5 9h11M6.5 15h11"/>
        </g>
      </svg>
      <span>www.glimworld-play.com</span>
    </div>
  </section>

</body>
</html>
```